VELTAR WEBSITE

need to create a new website for VELTAR ltd
the company deals with all aspects of safety products & safety wear
we need a simple website to show
ideas can be taken from following website whose products we shall distribute in kenya
www.kwr.co.uk
www.dorvik.eu
www.brimtoolsupplyco.com
www.gardvalewerks.co.za

we need following tabs
1) home - basic company information
2) products - broken down to following categories ie gloves, head protection, ear protection, mouth protection, foot protection
3) contacts

the company profile is a reputable company dealing with all aspects of safety, HSE (health and safety equipment), and PPE (personal protective equipment)

the website should have the dorvik logo for which we are an authorized distributor.
the dorvi industrial range writeup can be picked from their website
Updates

Dear Designers, i shall be able to choose a final design in 2 weeks, sorry i have not been able to finalise this due to a personal reason

Target Market(s)

the buyers are all types of industry who care for their employees safety

Industry/Entity Type

Industrial

Requirements
Must have
• clean look, fresh look, user freindly
Nice to have
• clear images, quick links etc

```html
<!DOCTYPE html>
<html lang="en">
<head>
<meta charset="utf-8">
<title>Veltar – Safety Products</title>
<link href="https://fonts.googleapis.com/css2?family=Signika:wght@300;400;600&display=swap" rel="stylesheet">
<style>
:root{
  --bg-top:#2a3a49;
  --bg-bottom:#4b5b6b;
  --card:#ffffff;
  --ink:#2f3a45;
  --ink-soft:#6b6f73;
  --gold:#d99c00;
  --gold-light:#f0b818;
  --rule:#e3e3e3;
  --tile:#dcdcdc;
  --footer-text:#e8edf2;
}
*{box-sizing:border-box;margin:0;padding:0}
html,body{width:966px;height:1200px;overflow:hidden}
body{
  position:relative;
  font-family:'Signika',sans-serif;
  background:linear-gradient(var(--bg-top),var(--bg-bottom));
  color:var(--ink);
}
.abs{position:absolute}
.page{position:absolute;left:97px;top:28px;width:773px;height:1079px;background:var(--card)}

/* header */
.brand{left:106px;top:60px;display:flex;align-items:center;gap:8px}
.brand-mark{width:22px;height:22px;background:var(--gold-light)}
.brand-name{font-size:26px;font-weight:600;color:var(--ink);letter-spacing:1px}
.brand-tag{left:107px;top:92px;font-size:7.5px;font-weight:600;color:var(--ink);text-transform:uppercase;letter-spacing:.3px;line-height:9px}
.account{top:50px;left:611px;font-size:11px;color:var(--ink-soft);display:flex;gap:8px;align-items:center}
.account .cart-count{color:var(--gold)}
.search{left:829px;top:43px;width:29px;height:22px;background:#e6e6e6;display:flex;align-items:center;justify-content:center}
.nav{top:98px;left:403px;font-size:11px;color:var(--ink)}
.nav span{position:absolute;white-space:nowrap}
.nav .sep{color:var(--ink)}
.nav .current{color:var(--gold)}
.nav-underline{left:394px;top:118px;width:49px;height:3px;background:var(--gold)}
.nav-caret{left:414px;top:113px;width:0;height:0;border-left:4px solid transparent;border-right:4px solid transparent;border-bottom:5px solid var(--gold)}

/* hero */
.hero{left:105px;top:134px;width:756px;height:310px;background:linear-gradient(90deg,#3a5c86 0%,#7a8796 35%,#c9c7c2 65%,#e6e3dd 100%)}
.hero-title{left:600px;top:202px;font-size:29px;font-weight:300;color:var(--ink)}
.hero-text{left:601px;top:256px;width:230px;font-size:10.5px;line-height:16px;color:var(--ink)}
.hero-btn{left:600px;top:340px;width:94px;height:26px;background:linear-gradient(var(--gold-light),var(--gold));border:1px solid #c18a00;font-size:10px;font-weight:600;color:#3a2a00;display:flex;align-items:center;justify-content:center}
.dot{top:422px;width:10px;height:10px;border-radius:50%;background:#7f8a95}
.dot.on{background:#2f3a45}

/* categories */
.cat-img{top:481px;width:241px;height:115px}
.cat-label{top:610px;font-size:15px;color:var(--ink)}
.rule{height:1px;background:var(--rule)}

/* featured */
.section-title{font-size:18px;color:var(--gold)}
.tile{top:720px;width:177px;height:97px;background:linear-gradient(#ececec,#d4d4d4)}
.tile-label{left:117px;top:733px;font-size:17px;line-height:24px;color:#fff;text-align:center}

/* welcome */
.welcome-title{left:107px;top:882px;font-size:18px;color:var(--ink)}
.copy{left:107px;width:496px;font-size:10.5px;line-height:16px;color:var(--ink-soft)}
.events-title{left:621px;top:882px;font-size:18px;color:var(--ink)}
.events-title em{font-style:normal;color:var(--gold)}
.event-date{left:621px;font-size:10.5px;color:var(--gold)}
.event-text{left:621px;width:240px;font-size:10.5px;line-height:16px;color:var(--ink-soft)}

/* footer */
.footer-nav{top:1138px;left:100px;font-size:10.5px;color:var(--footer-text)}
.footer-nav span{position:absolute;white-space:nowrap}
.copyright{left:100px;top:1161px;font-size:10.5px;color:var(--footer-text)}
.social{top:1138px;width:24px;height:24px;border-radius:50%;background:#8a939c;border:1px solid #a9b0b7}
</style>
</head>
<body>
<div class="page"></div>

<!-- header -->
<div class="abs brand"><span class="brand-mark"></span><span class="brand-name">VELTAR</span></div>
<div class="abs brand-tag">Specialized protective<br>&amp; industrial products</div>

<div class="abs account">
  <span>Register</span><span>|</span><span>Login</span><span>|</span>
  <svg width="14" height="12" viewBox="0 0 14 12"><path d="M0 1h3l2 7h7l2-5H4" fill="none" stroke="#d99c00" stroke-width="1.4"/><circle cx="6" cy="10.5" r="1.2" fill="#d99c00"/><circle cx="11" cy="10.5" r="1.2" fill="#d99c00"/></svg>
  <span>My Cart <span class="cart-count">(0) Item</span></span>
</div>
<div class="abs search"><svg width="14" height="14" viewBox="0 0 14 14"><circle cx="5.5" cy="5.5" r="4" fill="none" stroke="#2f3a45" stroke-width="1.8"/><path d="M8.5 8.5L13 13" stroke="#2f3a45" stroke-width="2.2"/></svg></div>

<nav class="abs nav">
  <span class="current" style="left:0">Home</span>
  <span class="sep" style="left:51px">|</span><span style="left:63px">About Us</span>
  <span class="sep" style="left:121px">|</span><span style="left:136px">Services</span>
  <span class="sep" style="left:191px">|</span><span style="left:206px">Products</span>
  <span class="sep" style="left:265px">|</span><span style="left:283px">Agencies</span>
  <span class="sep" style="left:341px">|</span><span style="left:356px">Clients</span>
  <span class="sep" style="left:404px">|</span><span style="left:419px">Contact</span>
</nav>
<div class="abs nav-caret"></div>
<div class="abs nav-underline"></div>

<!-- hero -->
<div class="abs hero" role="img" aria-label="Smiling worker in navy overalls holding a blue hard hat in an industrial plant"></div>
<h1 class="abs hero-title">Saftey Products</h1>
<p class="abs hero-text">Nemo enim ipsam voluptatem quia voluptas sit aspernatur aut odit aut fugit, sed qui consequ-untur magni dolores eos qui ratione voluptatem sequi nesciunt.</p>
<div class="abs hero-btn">Learn More &gt;&gt;</div>
<span class="abs dot on" style="left:793px"></span>
<span class="abs dot" style="left:807px"></span>
<span class="abs dot" style="left:823px"></span>
<span class="abs dot" style="left:838px"></span>

<!-- categories -->
<div class="abs cat-img" style="left:105px;background:linear-gradient(90deg,#1d3f7a,#4b6aa0 50%,#b8c63a)" role="img" aria-label="Worker in high-visibility jacket facing an oil refinery"></div>
<div class="abs cat-img" style="left:363px;background:linear-gradient(90deg,#5a4a6a,#9ab0c8 50%,#dfe6ee)" role="img" aria-label="Lab technician in mask handling test tubes"></div>
<div class="abs cat-img" style="left:620px;background:linear-gradient(90deg,#5b6a78,#e8612a 45%,#9aa4ad)" role="img" aria-label="Orange hard hat with safety tools and cones"></div>
<div class="abs cat-label" style="left:105px">Oil &amp; Industrial Works</div>
<div class="abs cat-label" style="left:363px">Medical &amp; Lab Safety</div>
<div class="abs cat-label" style="left:622px">Personal Safety Tools</div>
<div class="abs rule" style="left:105px;top:651px;width:754px"></div>

<!-- featured -->
<h2 class="abs section-title" style="left:105px;top:681px">Featured Products</h2>
<svg class="abs" style="left:835px;top:684px" width="26" height="16" viewBox="0 0 26 16"><path d="M8 0v16L0 8z" fill="#2f3a45"/><path d="M18 0v16l8-8z" fill="#2f3a45"/></svg>
<div class="abs tile" style="left:105px;background:linear-gradient(90deg,#8f8f8f,#c7683a 60%,#a9a9a9)" role="img" aria-label="Safety kit with orange helmet, earmuffs, goggles and gloves"></div>
<div class="abs tile-label">latest<br>Saftey Kit</div>
<div class="abs tile" style="left:298px" role="img" aria-label="Teal and grey ear defenders"></div>
<div class="abs tile" style="left:491px" role="img" aria-label="Life vests and protective gloves"></div>
<div class="abs tile" style="left:684px" role="img" aria-label="Tan safety work boots"></div>
<div class="abs rule" style="left:107px;top:857px;width:752px"></div>

<!-- welcome -->
<h2 class="abs welcome-title">Welcome to our site..</h2>
<p class="abs copy" style="top:920px">Sed ut perspiciatis unde omnis istes natus error sit voluptatem accusantiumai doloremque laudantiumas, totam rem aperiam, eaque ipsa quae ab ill inventore veritatis et quasi architect beatae vitae dicta suntasi explicabo quae ab ill inventore veritatis et quasi architec.</p>
<p class="abs copy" style="top:987px">Sed ut perspiciatis unde omnis istes natus error sit voluptatem accusantiumai doloremque laudantiumas, totam rem aperiam, eaque ipsa quae ab ill inventore veritatis et quasi architect beatae vitae dicta suntasi explicabo. Sed ut perspiciaitis unde omnis istes natus error sit voluptatem accusantium doloremque laud antium, totam rem aperiam, eaque ipsa quae ab ill inventore veritatis et quasiasi architect beatae vitae dicta sunt explicabo&nbsp; architect natus error sit voluptatemnatus error sit voluptatem.</p>
<div class="abs rule" style="left:611px;top:881px;width:1px;height:186px"></div>

<h2 class="abs events-title">Latest <em>Events</em></h2>
<svg class="abs" style="left:841px;top:894px" width="16" height="10" viewBox="0 0 16 10"><path d="M5 1L1 5l4 4M11 1l4 4-4 4" fill="none" stroke="#2f3a45" stroke-width="1.5"/></svg>
<div class="abs event-date" style="top:920px">05 Dec 2013</div>
<p class="abs event-text" style="top:938px">Sed ut perspiciatis unde omnis istes natus error sit voluptatem accusantiumai unde omnis</p>
<div class="abs rule" style="left:621px;top:986px;width:240px"></div>
<div class="abs event-date" style="top:1001px">05 Dec 2013</div>
<p class="abs event-text" style="top:1019px">Sed ut perspiciatis unde omnis istes natus error sit voluptatem accusantiumai unde omnis</p>

<!-- footer -->
<nav class="abs footer-nav">
  <span style="left:0">Home</span><span style="left:40px">|</span>
  <span style="left:53px">About Us</span><span style="left:106px">|</span>
  <span style="left:116px">Services</span><span style="left:167px">|</span>
  <span style="left:178px">Products</span><span style="left:235px">|</span>
  <span style="left:248px">Agencies</span><span style="left:303px">|</span>
  <span style="left:316px">Clients</span><span style="left:359px">|</span>
  <span style="left:372px">Contact</span>
</nav>
<div class="abs copyright">(c) 2013. Veltar All Right Reserved.</div>
<span class="abs social" style="left:753px"></span>
<span class="abs social" style="left:781px"></span>
<span class="abs social" style="left:809px"></span>
<span class="abs social" style="left:837px"></span>
</body>
</html>
```